Business Card Design

Need a new business card to represent our legal vertical focus. attached is an example of our old business card and newest logo. we would like the card to also identify "Legal Tech" as a tag line of business.

Our new address is
4817 Marlowe Hatchfield Rd.
Suite 518
Cincinnati, OH 45917

we no longer have a fax number.

Target Market(s)

Tech Consulting for Law Firms

Industry/Entity Type

Legal

Contact Information for Business Card

should use logo and colors. we are a b2b company

Font styles to use
Other font styles liked:
• tahoma

Requirements
Must have
• all print should be in lower case just as shown in photos. tag line should not
Should not have
• pinstripes or drop shadows

```html
<!DOCTYPE html>
<html lang="en">
<head>
<meta charset="utf-8">
<title>Tracewire Legal Tech — Business Card</title>
<link rel="stylesheet" href="https://fonts.googleapis.com/css2?family=Lato:wght@400;700&display=swap">
<style>
  :root {
    --canvas-bg: #2e2e2e;
    --card-bg: #1b1b1c;
    --card-bg-alt: #202021;
    --text-light: #f2f2f2;
    --text-muted: #c9c9c9;
    --accent: #e8461c;
  }
  * { box-sizing: border-box; margin: 0; padding: 0; }
  html, body {
    width: 1200px;
    height: 900px;
    overflow: hidden;
    background: var(--canvas-bg);
    font-family: "Lato", Tahoma, sans-serif;
  }
  .canvas {
    position: relative;
    width: 1200px;
    height: 900px;
    display: flex;
    align-items: center;
    justify-content: center;
    gap: 44px;
  }
  .card {
    position: relative;
    width: 500px;
    height: 286px;
    border-radius: 22px;
    background: var(--card-bg);
    overflow: hidden;
  }
  /* contact side */
  .card--contact { background: var(--card-bg-alt); }
  .card__mark {
    position: absolute;
    left: 92px;
    top: 113px;
    width: 60px;
    height: 60px;
    background: var(--accent);
  }
  .contact {
    position: absolute;
    left: 246px;
    top: 62px;
    right: 24px;
    color: var(--text-light);
    line-height: 1.3;
    white-space: nowrap;
  }
  .contact__name {
    font-size: 23px;
    font-weight: 400;
    letter-spacing: 0.2px;
  }
  .contact__title {
    font-size: 14px;
    color: var(--accent);
    margin-bottom: 14px;
  }
  .contact__address {
    font-size: 14.5px;
    font-style: normal;
    margin-bottom: 14px;
  }
  .contact__lines { list-style: none; font-size: 14.5px; }
  .contact__label { color: var(--accent); margin-right: 4px; }

  /* logo side */
  .brand {
    position: absolute;
    inset: 0;
    display: flex;
    flex-direction: column;
    align-items: center;
    justify-content: center;
  }
  .brand__row { display: flex; align-items: center; gap: 14px; }
  .brand__dot {
    width: 22px;
    height: 22px;
    border-radius: 50%;
    background: var(--text-light);
  }
  .brand__name {
    font-size: 54px;
    font-weight: 700;
    color: var(--text-light);
    letter-spacing: -0.5px;
  }
  .brand__tagline {
    margin-top: 4px;
    margin-left: 36px;
    font-size: 17px;
    font-weight: 400;
    letter-spacing: 11px;
    color: var(--text-muted);
  }
</style>
</head>
<body>
<main class="canvas">
  <section class="card card--contact" aria-label="Business card, contact side">
    <div class="card__mark" aria-hidden="true"></div>
    <div class="contact">
      <h1 class="contact__name">daniel Kerrow</h1>
      <p class="contact__title">managing director</p>
      <address class="contact__address">4817 Marlowe Hatchfield Rd.<br>Suite 518, Cincinnati, OH 45917</address>
      <ul class="contact__lines">
        <li><span class="contact__label">T:</span>513-555 0148</li>
        <li><span class="contact__label">E:</span>info@tracewire.com</li>
        <li><span class="contact__label">W:</span>www.tracewire.com</li>
      </ul>
    </div>
  </section>

  <section class="card card--brand" aria-label="Business card, logo side">
    <div class="brand">
      <div class="brand__row">
        <span class="brand__dot" aria-hidden="true"></span>
        <span class="brand__name">Tracewire</span>
      </div>
      <p class="brand__tagline">Legal Tech</p>
    </div>
  </section>
</main>
</body>
</html>
```